Business Card Design

New business card design

Target Market(s)

Residential & Commercial Property Managers

Industry/Entity Type

Plumbing Services

Contact Information for Business Card

Name - Rowan Keddle, title - Director, Phone Number - 0431 286 517, email - rowan@tbk-plumbing.com.au, Company ABN - 73 215 904 386,

Font styles to use
Sans Serif

Colors
0054AA
0677BA
7BADD7
CADEEF
E8F1F8

```html
<!DOCTYPE html>
<html lang="en">
<head>
<meta charset="utf-8">
<title>TBK Plumbing Services – Business Card</title>
<link href="https://fonts.googleapis.com/css2?family=Lato:wght@300;400;700&family=Oswald:wght@600&display=swap" rel="stylesheet">
<style>
  :root {
    --bg: #2a2c30;
    --card-dark: #1f2530;
    --card-light: #ffffff;
    --brand-blue: #1a9be0;
    --ink: #23272e;
    --logo-grey: #b4bbc4;
  }
  * { box-sizing: border-box; margin: 0; padding: 0; }
  html, body { width: 1200px; height: 875px; overflow: hidden; background: var(--bg); }
  .canvas {
    position: relative; width: 1200px; height: 875px;
    display: flex; align-items: center; justify-content: center; gap: 40px;
  }
  .card {
    position: relative; width: 520px; height: 298px; border-radius: 16px;
    box-shadow: 0 18px 40px rgba(0,0,0,.45);
  }
  .card--front { background: var(--card-dark); display: flex; align-items: center; justify-content: center; }
  .brand { display: flex; align-items: center; gap: 14px; }
  .brand__dot { width: 18px; height: 18px; border-radius: 50%; background: var(--brand-blue); }
  .brand__name {
    font-family: 'Lato', sans-serif; font-weight: 300; font-size: 30px;
    letter-spacing: 3px; color: var(--logo-grey);
  }
  .card--back { background: var(--card-light); font-family: 'Lato', sans-serif; color: var(--ink); }
  .holder { position: absolute; left: 38px; top: 118px; width: 200px; text-align: right; }
  .holder__name {
    font-family: 'Oswald', sans-serif; font-weight: 600; font-size: 34px;
    line-height: 1; color: var(--brand-blue); letter-spacing: -0.5px; text-transform: uppercase;
  }
  .holder__title { font-size: 15px; margin-top: 4px; }
  .divider { position: absolute; left: 258px; top: 92px; width: 2px; height: 118px; background: var(--brand-blue); }
  .details { position: absolute; left: 278px; top: 90px; font-size: 12.5px; line-height: 1.35; }
  .details__row { display: flex; align-items: flex-start; gap: 8px; }
  .details__row + .details__row { margin-top: 4px; }
  .details__company { font-weight: 700; }
  .details svg { flex: none; width: 12px; height: 12px; margin-top: 2px; fill: var(--brand-blue); }
  .abn { position: absolute; left: 0; right: 0; bottom: 42px; text-align: center; font-size: 13px; }
</style>
</head>
<body>
<main class="canvas">
  <section class="card card--front" aria-label="Card front">
    <div class="brand">
      <span class="brand__dot"></span>
      <span class="brand__name">TBK Plumbing Services</span>
    </div>
  </section>

  <section class="card card--back" aria-label="Card back">
    <div class="holder">
      <p class="holder__name">Rowan Keddle</p>
      <p class="holder__title">Director</p>
    </div>
    <div class="divider"></div>
    <div class="details">
      <div class="details__row">
        <svg viewBox="0 0 12 12"><path d="M6 0a4 4 0 0 0-4 4c0 3 4 8 4 8s4-5 4-8a4 4 0 0 0-4-4zm0 5.6A1.6 1.6 0 1 1 6 2.4a1.6 1.6 0 0 1 0 3.2z"/></svg>
        <div>
          <p class="details__company">TBK Plumbing Services Pty Ltd</p>
          <p>Unit 7/22 Harbour Lane</p>
          <p>Greenhaven NSW 2041</p>
        </div>
      </div>
      <div class="details__row">
        <svg viewBox="0 0 12 12"><path d="M2.4 0.5l2 2-1 1.4a7 7 0 0 0 4.7 4.7l1.4-1 2 2-1.3 1.9C5 11 1 7 .5 1.8z"/></svg>
        <p>0431 286 517</p>
      </div>
      <div class="details__row">
        <svg viewBox="0 0 12 12"><path d="M0 2h12v1L6 7 0 3zM0 4.5l6 4 6-4V10H0z"/></svg>
        <p>rowan@tbk-plumbing.com.au</p>
      </div>
      <div class="details__row">
        <svg viewBox="0 0 12 12"><path d="M6 0a6 6 0 1 0 0 12A6 6 0 0 0 6 0zm0 1.2c.8 0 1.6 2 1.7 4.2H4.3C4.4 3.2 5.2 1.2 6 1.2zM4.3 6.6h3.4C7.6 8.8 6.8 10.8 6 10.8S4.4 8.8 4.3 6.6z"/></svg>
        <p>tbkplumbingservices.com.au</p>
      </div>
    </div>
    <p class="abn">ABN - 73 215 904 386</p>
  </section>
</main>
</body>
</html>
```